We are a new company with 2 divisions a medical research and medical product sales. We need a company logo and Business Cards. The design files need to be provided to us in Adobe Photoshop CS 5.1.

Target Market(s)

Medical Community

Industry/Entity Type

Medical

Contact Information for Business Card

Company Name - Harrowgate Lifesciences LLC
Company Address 4127 Larkspur Ave Suite 7, Westbury Oaks Ga 31092

Requirements
Must have
• The design files need to be provided to us in Adobe Photoshop CS 5.1.

```html
<!DOCTYPE html>
<html lang="en">
<head>
<meta charset="utf-8">
<title>Harrowgate Lifesciences LLC – Business Card</title>
<link rel="stylesheet" href="https://fonts.googleapis.com/css2?family=EB+Garamond:wght@400;500&display=swap">
<style>
  :root {
    --brand-red: #ff0000;
    --card-white: #ffffff;
    --ink: #1a1a1a;
    --backdrop: #e9e7e4;
  }
  * { margin: 0; padding: 0; box-sizing: border-box; }
  html, body {
    width: 1200px;
    height: 900px;
    overflow: hidden;
    background: var(--backdrop);
  }
  .canvas {
    position: relative;
    width: 1200px;
    height: 900px;
  }
  .business-card {
    position: absolute;
    left: 110px;
    top: 170px;
    width: 980px;
    height: 560px;
    background: var(--card-white);
    font-family: "EB Garamond", "Times New Roman", serif;
    color: var(--ink);
    box-shadow: 0 10px 30px rgba(0,0,0,0.12);
    overflow: hidden;
  }
  .brand-band {
    position: absolute;
    left: 0; top: 0;
    width: 100%;
    height: 190px;
    background: var(--brand-red);
    display: flex;
    align-items: center;
    padding-left: 32px;
  }
  .brand-disc {
    width: 150px;
    height: 150px;
    border-radius: 50%;
    background: var(--card-white);
    flex: none;
  }
  .brand-name {
    margin-left: 14px;
    color: var(--card-white);
    font-size: 54px;
    font-weight: 400;
    line-height: 0.98;
    text-transform: uppercase;
    letter-spacing: 0.5px;
  }
  .contact {
    position: absolute;
    left: 44px;
    top: 230px;
  }
  .person-name {
    color: var(--brand-red);
    font-size: 44px;
    font-weight: 400;
    line-height: 1;
  }
  .person-title {
    font-size: 29px;
    line-height: 1.1;
    margin-top: 2px;
  }
  .details {
    margin-top: 44px;
    font-size: 29px;
    line-height: 1.05;
    list-style: none;
  }
</style>
</head>
<body>
<main class="canvas">
  <article class="business-card">
    <header class="brand-band">
      <div class="brand-disc"></div>
      <h1 class="brand-name">Harrowgate<br>Lifesciences LLC.</h1>
    </header>
    <section class="contact">
      <h2 class="person-name">Daniel Reeve</h2>
      <p class="person-title">Chief Executive Officer</p>
      <ul class="details">
        <li>4127 Larkspur Ave Suite 7</li>
        <li>Westbury Oaks Ga 31092</li>
        <li>Phone: 352 555 0147</li>
        <li>Email: d.reeve@harrowgatels.com</li>
        <li>www.harrowgatels.com</li>
      </ul>
    </section>
  </article>
</main>
</body>
</html>
```